Investment company needing business card

We are wanting a business card which looks sharp and easy on the eye. We are thinking of having a business card with the logo embossed on it, to really make it stand out. We will only have a small amount of information of the business card, person's name, position, email address and phone number

Contact Information for Business Card

Danielle Frost
Executive Assistant
+64 21 473 5162
danielf@harwickpartners.co.nz

Requirements
Must have
• Embossed logo
Should not have
• Not to be busy

```html
<!DOCTYPE html>
<html lang="en">
<head>
<meta charset="UTF-8">
<title>Harwick Partners – Business Card</title>
<link href="https://fonts.googleapis.com/css2?family=Open+Sans:wght@400;600;700&display=swap" rel="stylesheet">
<style>
  :root {
    --stage: #1c1c1c;
    --card: #424142;
    --ink: #ffffff;
    --ink-soft: #e4e4e4;
    --rule: #8a8a8a;
  }
  * { margin: 0; padding: 0; box-sizing: border-box; }
  html, body { width: 1200px; height: 900px; overflow: hidden; }
  body {
    background: var(--stage);
    font-family: "Open Sans", Arial, sans-serif;
    display: flex;
    flex-direction: column;
    align-items: center;
    justify-content: center;
    gap: 44px;
  }
  .card {
    width: 620px;
    height: 354px;
    background: var(--card);
    border-radius: 22px;
    box-shadow: 0 14px 30px rgba(0,0,0,0.45);
    position: relative;
  }
  /* contact side */
  .card--contact {
    display: flex;
    align-items: center;
    justify-content: center;
  }
  .identity {
    text-align: right;
    padding-right: 22px;
  }
  .identity__name {
    font-weight: 700;
    font-size: 21px;
    color: var(--ink);
    text-transform: uppercase;
    letter-spacing: 0.2px;
  }
  .identity__role {
    font-size: 15px;
    color: var(--ink-soft);
    margin-top: 2px;
  }
  .divider {
    width: 1px;
    height: 74px;
    background: var(--rule);
  }
  .contact-list {
    list-style: none;
    padding-left: 20px;
  }
  .contact-list li {
    display: flex;
    align-items: center;
    gap: 9px;
    font-size: 14px;
    color: var(--ink-soft);
    line-height: 23px;
  }
  .contact-list svg { width: 12px; height: 12px; flex: none; }
  /* brand side */
  .card--brand {
    display: flex;
    align-items: center;
    justify-content: center;
    gap: 16px;
  }
  .brand__mark {
    width: 26px;
    height: 26px;
    background: var(--ink);
  }
  .brand__name {
    font-weight: 600;
    font-size: 40px;
    color: var(--ink);
    letter-spacing: 2px;
    text-transform: uppercase;
  }
</style>
</head>
<body>
  <section class="card card--contact" aria-label="Card front with contact details">
    <div class="identity">
      <p class="identity__name">Danielle Frost</p>
      <p class="identity__role">Executive Assistant</p>
    </div>
    <div class="divider"></div>
    <ul class="contact-list">
      <li>
        <svg viewBox="0 0 12 12" aria-hidden="true"><path d="M2.5 1 L4.5 3.2 L3.4 4.5 Q4.6 7 7.4 8.6 L8.7 7.4 L11 9.4 L9.8 11 Q4.5 10.5 1 2.3 Z" fill="#fff"/></svg>
        +64 21 473 5162
      </li>
      <li>
        <svg viewBox="0 0 12 12" aria-hidden="true"><rect x="0.5" y="2" width="11" height="8" fill="#fff"/><path d="M0.5 2 L6 6.5 L11.5 2" fill="none" stroke="#424142" stroke-width="1"/></svg>
        danielf@harwickpartners.co.nz
      </li>
      <li>
        <svg viewBox="0 0 12 12" aria-hidden="true"><circle cx="6" cy="6" r="5.2" fill="none" stroke="#fff" stroke-width="1.2"/><ellipse cx="6" cy="6" rx="2.2" ry="5.2" fill="none" stroke="#fff" stroke-width="1"/><line x1="0.8" y1="6" x2="11.2" y2="6" stroke="#fff" stroke-width="1"/></svg>
        www.harwickpartners.co.nz
      </li>
    </ul>
  </section>

  <section class="card card--brand" aria-label="Card back with company name">
    <span class="brand__mark" aria-hidden="true"></span>
    <span class="brand__name">Harwick Partners</span>
  </section>
</body>
</html>
```